ORLA - Óptica Médica - web design and concept

Website concept - Create and develop our website design and structure. ORLA is an optical store chain, and we are looking to establish our web and digital concept. In attachment there are several pictures about our stores and our logo.

The website structure should be user friendly. Colors should be light and the design as simple and minimalist as possible. There are different variations of the logothat can be used, check the file.

The website will include optical collections and sun collections as an online store. Also, a medical menu should be considered in order for clients to schedule optometry appointments. There should also be a menu for client assistance where the clients can read about glass maintenance in our workshop.
Updates

Low design quality

Number of Pages Required

5+ page

Font styles to use
Serif
Sans Serif

Requirements
Must have
• Must be user-friendly and minimalist.
• Please USE PICTURES FROM THE BRANDS we sell: MERUN, BOSKA, PNW, KOLE, BAMPE
Nice to have
• Nice to inspire: ZEK glasses (see website https://ch.shopzek.com/en/)
• Nice to inspire: https://merun-eyewear.com/
• Nice to ispire: https://www.pnwglobe.com/en/
Should not have
• Hysteric colors and shapes

```html
<!DOCTYPE html>
<html lang="en">
<head>
<meta charset="utf-8">
<title>ORLA Óptica Médica — Contact Us</title>
<link rel="stylesheet" href="https://fonts.googleapis.com/css2?family=Lato:wght@300;400;700&display=swap">
<style>
:root{
  --ink:#1a1a1a;
  --text:#444;
  --muted:#777;
  --gold:#ebb75a;
  --gold-dark:#d9a13f;
  --line:#e3e3e3;
  --paper:#ffffff;
  --footer:#000000;
  --map-sea:#a9d3f5;
  --map-land:#cfe0b8;
}
*{box-sizing:border-box;margin:0;padding:0}
html,body{width:1200px;height:2206px;overflow:hidden;background:var(--paper)}
body{position:relative;font-family:'Lato',sans-serif;color:var(--text)}
.abs{position:absolute}

/* hero */
.hero-photo{left:353px;top:0;width:847px;height:606px;
  background:linear-gradient(90deg,#ffffff 0%,#e9e4e0 18%,#6b5148 45%,#3a2a25 70%,#f1ece8 100%)}
.hero-title{left:157px;top:296px;font-size:45px;font-weight:300;color:var(--ink);letter-spacing:.5px}

/* header */
.social{left:160px;top:16px;display:flex;gap:10px}
.social span{width:10px;height:10px;border-radius:50%;background:var(--ink);display:block}
.brand{left:540px;top:12px;width:120px;text-align:center;color:var(--ink)}
.brand-mark{width:30px;height:30px;border:1.5px solid var(--ink);margin:0 auto 8px}
.brand-name{font-size:19px;letter-spacing:4px;font-weight:400}
.brand-sub{font-size:5px;letter-spacing:2px;margin-top:1px}
.cart{left:820px;top:15px;font-size:10.5px;color:var(--ink);display:flex;align-items:center;gap:6px}
.phone-top{left:937px;top:15px;font-size:10.5px;color:var(--ink);display:flex;align-items:center;gap:6px}
.nav{left:468px;top:102px;display:flex;align-items:center;gap:0;font-size:11px;color:var(--ink)}
.nav a{color:inherit;text-decoration:none;margin-right:19px}
.nav a.active{color:var(--gold)}
.nav .cta{background:var(--gold);padding:4px 11px;margin:0;color:var(--ink)}

/* info */
.block-title{font-size:25px;font-weight:300;color:var(--ink)}
.info-line{font-size:11px;color:var(--text);line-height:22.5px}
.map{left:602px;top:676px;width:438px;height:249px;
  background:linear-gradient(100deg,var(--map-land) 0%,var(--map-land) 22%,var(--map-sea) 30%,var(--map-sea) 58%,var(--map-land) 68%,var(--map-land) 100%)}

/* form */
.section-title{left:0;top:1034px;width:1200px;text-align:center;font-size:44px;font-weight:300;color:var(--ink)}
.label{font-size:10.5px;color:var(--text)}
.field{border:2px solid var(--line);background:#fff}
.send{left:165px;top:1752px;width:182px;height:52px;background:var(--gold);border:1px solid var(--gold-dark);
  font-size:13px;color:var(--ink);display:flex;align-items:center;justify-content:center;letter-spacing:.3px}

/* footer */
.footer{left:0;top:1885px;width:1200px;height:321px;background:var(--footer);color:#fff}
.f-brand{left:161px;top:56px;color:var(--gold);font-size:17px;letter-spacing:3px}
.f-about{left:161px;top:118px;width:160px;font-size:10.5px;line-height:12px}
.f-more{left:161px;top:165px;font-size:10px}
.f-social{left:161px;top:191px;display:flex;gap:10px}
.f-social span{width:9px;height:9px;border-radius:50%;background:var(--gold);display:block}
.f-head{top:88px;font-size:13px;font-weight:700;color:var(--gold)}
.f-list{top:123px;list-style:none;font-size:10.5px;line-height:16.5px}
.f-list li::before{content:"•";color:var(--gold);margin-right:10px}
.f-contact{left:859px;top:123px;font-size:10.5px;line-height:16.5px}
.f-contact div{display:flex;gap:8px;align-items:flex-start;margin-bottom:8px}
.f-rule{left:161px;top:225px;width:880px;height:1px;background:#555}
.f-copy{left:161px;top:242px;font-size:12px}
.f-legal{left:820px;top:236px;width:221px;text-align:right;font-size:12px}
</style>
</head>
<body>

<div class="abs hero-photo" role="img" aria-label="Photograph of a woman with long wavy hair wearing round sunglasses"></div>
<h1 class="abs hero-title">Contact Us</h1>

<header>
  <div class="abs social" aria-label="Social links"><span></span><span></span><span></span><span></span><span></span></div>
  <div class="abs brand">
    <div class="brand-mark"></div>
    <div class="brand-name">ORLA</div>
    <div class="brand-sub">OPTICA MEDICA</div>
  </div>
  <div class="abs cart">
    <svg width="10" height="11" viewBox="0 0 10 11"><path d="M2 4h6l1 7H1z" fill="#1a1a1a"/><path d="M3 4V2.5a2 2 0 0 1 4 0V4" stroke="#1a1a1a" fill="none"/></svg>
    Your Cart &nbsp;( 0 )
  </div>
  <div class="abs phone-top">
    <svg width="10" height="10" viewBox="0 0 10 10"><path d="M2 0l2 2.5-1 1.3a6 6 0 0 0 3.2 3.2l1.3-1L10 8l-1.5 2C4 10 0 6 0 1.5z" fill="#1a1a1a"/></svg>
    +000-555-0142
  </div>
  <nav class="abs nav">
    <a href="#">Home</a><a href="#">Sun</a><a href="#">Optical</a><a href="#" class="active">Store</a><a href="#">Contact Us</a>
    <span class="cta">Make an Appoinment</span>
  </nav>
</header>

<section>
  <h2 class="abs block-title" style="left:161px;top:712px">Call Us</h2>
  <div class="abs info-line" style="left:164px;top:752px">Telephone &nbsp;: +000-555-0188<br>Mobile &nbsp;: +000-555-0188</div>
  <h2 class="abs block-title" style="left:161px;top:831px">Mail Us</h2>
  <div class="abs info-line" style="left:164px;top:864px">E-Mail &nbsp;: info@orlaopticamedica.com</div>

  <h2 class="abs block-title" style="left:406px;top:712px">Opening Hours</h2>
  <div class="abs info-line" style="left:410px;top:752px">Monday – 3:00pm – 7:30pm<br>Tuesday – Saturday<br>10:00am – 1:00pm<br>3:00pm – 7:30pm</div>
  <div class="abs info-line" style="left:410px;top:864px">[Friday closed]</div>

  <div class="abs map" role="img" aria-label="Map of the North Atlantic showing the store location"></div>
</section>

<section>
  <h2 class="abs section-title">Send Us Your Feedback</h2>
  <div class="abs label" style="left:163px;top:1108px">Name</div>
  <div class="abs field" style="left:161px;top:1130px;width:880px;height:69px"></div>
  <div class="abs label" style="left:163px;top:1230px">E-Mail Address</div>
  <div class="abs field" style="left:161px;top:1250px;width:880px;height:69px"></div>
  <div class="abs label" style="left:163px;top:1351px">Subject</div>
  <div class="abs field" style="left:161px;top:1370px;width:433px;height:69px"></div>
  <div class="abs label" style="left:607px;top:1351px">Phone Number</div>
  <div class="abs field" style="left:606px;top:1370px;width:435px;height:69px"></div>
  <div class="abs label" style="left:163px;top:1468px">Massage</div>
  <div class="abs field" style="left:161px;top:1489px;width:880px;height:223px"></div>
  <div class="abs send">SEND MASSAGE</div>
</section>

<footer class="abs footer">
  <div class="abs f-brand">ORLA</div>
  <p class="abs f-about">Lorem Ipsum is simply dummy text of the printing and typesetting industry.</p>
  <div class="abs f-more">READ MORE.....</div>
  <div class="abs f-social"><span></span><span></span><span></span><span></span><span></span></div>

  <h3 class="abs f-head" style="left:423px">QUICK LINK</h3>
  <ul class="abs f-list" style="left:423px"><li>Women</li><li>Men</li><li>Youth</li><li>Collections</li><li>Contact Us</li></ul>

  <h3 class="abs f-head" style="left:635px">ACCOUNT</h3>
  <ul class="abs f-list" style="left:635px"><li>My Account</li><li>My Wishlist</li><li>Checkout</li><li>Create Account</li><li>Register</li></ul>

  <h3 class="abs f-head" style="left:859px">QUICK CONTACT</h3>
  <div class="abs f-contact">
    <div><svg width="9" height="9" viewBox="0 0 10 10"><path d="M2 0l2 2.5-1 1.3a6 6 0 0 0 3.2 3.2l1.3-1L10 8l-1.5 2C4 10 0 6 0 1.5z" fill="#ebb75a"/></svg>+000-555-0188</div>
    <div><svg width="10" height="8" viewBox="0 0 10 8" style="margin-top:4px"><rect width="10" height="8" fill="#ebb75a"/><path d="M0 0l5 4 5-4" stroke="#000" fill="none"/></svg>info@orlaopticamedica.com</div>
    <div><svg width="9" height="12" viewBox="0 0 9 12" style="margin-top:2px"><path d="M4.5 12S0 6.8 0 4.5a4.5 4.5 0 0 1 9 0C9 6.8 4.5 12 4.5 12z" fill="#ebb75a"/><circle cx="4.5" cy="4.5" r="1.6" fill="#000"/></svg><span>14 Alder Lane,<br>Brookfield Township, NJ 00000</span></div>
  </div>

  <div class="abs f-rule"></div>
  <div class="abs f-copy">CopyRight &nbsp;©2018 Orla Optica Medica. All Right Reserve</div>
  <div class="abs f-legal">Privacy Policy - Terms &amp; Conditions</div>
</footer>

</body>
</html>
```